A start-up named "Corvane Therapeutics" - needs a new PowerPoint design

We need a new PowerPoint Design for an early-stage start-up named "Corvane Therapeutics" seeking to disrupt the current approach towards drug discovery within aging disorders.

We would like to build on Corvane's legacy, the founder of the modern science of genetics, by employing a multidisciplinary approach, experimenting, and providing elderly patients the attention they deserve.

We have selected the suffix "therapeutics" intentionally as it stands for (a medicine) the treatment of disease; the science of healing. Alzheimer’s treatment is a huge, urgent, unmet need:
- Shift from a disease-management system to a preventive medicine system
- Focus on increasing the health span, not only the life span

Target Market(s)

Pharma/ Biotech Executives Medical Institutions Healthcare professionals (MDs, nurses, payors, pharmacists, etc.) Patients

Industry/Entity Type

Healthcare

Other font styles liked:
• Celias

Colors
0054AA
0677BA
7BADD7
CADEEF
E8F1F8
E54698
E96AAD
F1A4CE
F9D9EA
FCEFF6
A7469A
B969AE
D3A5CF
EDDBEB
F8F0F9
6B429C
8869AF
B7A5CE
E3DAEB
F3F0F8

Requirements
Must have
• - differentiate from other companies named after Corvane - differentiate from other Pharma/ Biotech companies
Nice to have
• simplicity/ minimalist logo vivid colors gradient 3D Life-Sciences inspired Simple geometry Balance
Should not have
• mascot/ emblem watermark logo animated ink style nature-inspired inventive typography artistic chaos

```html
<!DOCTYPE html>
<html lang="en">
<head>
<meta charset="utf-8">
<title>Corvane Therapeutics – Presentation Design</title>
<link href="https://fonts.googleapis.com/css2?family=Poppins:wght@400;500;600;700;800&display=swap" rel="stylesheet">
<style>
  :root{
    --stage:#000;
    --plum-deep:#5a0c3d;
    --plum:#7a1551;
    --plum-bright:#8f1f62;
    --orange:#f29a1f;
    --gold:#f5c21b;
    --amber:#e8891c;
    --grey:#9b9b9b;
    --grey-light:#d9d9d9;
    --white:#ffffff;
    --ink:#2b1a24;
    --pink:#e0307f;
  }
  *{box-sizing:border-box;margin:0;padding:0}
  html,body{width:1200px;height:1006px;overflow:hidden;background:var(--stage)}
  body{position:relative;font-family:"Poppins",sans-serif;color:var(--white)}
  .slide{position:absolute;width:451px;height:253px;overflow:hidden;
    background:radial-gradient(ellipse at 45% 40%,var(--plum-bright) 0%,var(--plum) 45%,var(--plum-deep) 100%)}
  .col-left{left:140px}.col-right{left:609px}
  .row-1{top:95px}.row-2{top:376px}.row-3{top:658px}
  .abs{position:absolute}
  .band{position:absolute;left:0;right:0;top:20px;height:13px;
    background:linear-gradient(90deg,var(--amber),var(--gold) 55%,var(--amber))}
  .brand-tab{position:absolute;left:287px;top:0;width:117px;height:51px;background:var(--white);
    clip-path:polygon(0 0,100% 0,100% 90%,0 100%);display:flex;align-items:center;gap:6px;padding:0 10px}
  .brand-mark{width:10px;height:10px;background:var(--plum);flex:none}
  .brand-name{color:var(--plum);font-weight:600;line-height:1}
  .brand-tab .brand-name span{display:block}
  .brand-tab .word-main{font-size:16px}
  .brand-tab .word-sub{font-size:7px;letter-spacing:.9px;margin-top:2px}
  .small{font-size:4.2px;line-height:1.35;text-align:center;color:#f3dbe7}
  .body{font-size:6.3px;line-height:1.25;color:#f7e6ef}
  .head-gold{color:var(--gold);font-weight:800;letter-spacing:2.4px;font-size:16px;line-height:1}
  .label{font-size:4.6px;font-weight:500;letter-spacing:.3px;text-align:center}

  /* cover */
  .cover{background:var(--white)}
  .cover-band{position:absolute;left:0;right:0;top:194px;height:22px;
    background:linear-gradient(90deg,var(--plum-deep),var(--plum-bright) 50%,var(--plum-deep))}
  .cover-brand{position:absolute;left:78px;top:64px;display:flex;align-items:center;gap:18px}
  .cover-brand .brand-mark{width:34px;height:34px}
  .cover-brand .word-main{display:block;font-size:56px;letter-spacing:-.5px}
  .cover-brand .word-sub{display:block;font-size:22px;letter-spacing:3px;margin-top:4px}

  /* market list */
  .market-title{font-size:16.5px;font-weight:700;letter-spacing:-.2px}
  .market-item h4{font-size:6.6px;font-weight:700;line-height:1}
  .market-item p{font-size:5.5px;line-height:1.2;color:#f7e6ef;margin-top:1px}
  .num{font-size:10px;font-weight:600;line-height:1}
</style>
</head>
<body>

<!-- Cover -->
<section class="slide col-left row-1 cover">
  <div class="cover-band"></div>
  <div class="cover-brand">
    <div class="brand-mark"></div>
    <div class="brand-name"><span class="word-main">Corvane</span><span class="word-sub">Therapeutics</span></div>
  </div>
</section>

<!-- Key figures -->
<section class="slide col-right row-1">
  <div class="band"></div>
  <div class="brand-tab"><div class="brand-mark"></div><div class="brand-name"><span class="word-main">Corvane</span><span class="word-sub">Therapeutics</span></div></div>
  <svg class="abs" style="left:0;top:0" width="451" height="253" viewBox="0 0 451 253">
    <g fill="none" stroke-width="2.6" stroke-linecap="round">
      <line x1="99" y1="69" x2="99" y2="214" stroke="#c9a3b8" stroke-width=".7"/>
      <line x1="170" y1="69" x2="170" y2="214" stroke="#c9a3b8" stroke-width=".7"/>
      <line x1="285" y1="71" x2="285" y2="155" stroke="#e9cfdc" stroke-width=".8"/>
      <line x1="285" y1="164" x2="285" y2="214" stroke="#e9cfdc" stroke-width=".8"/>
      <circle cx="64" cy="90" r="17" stroke="var(--grey)" stroke-dasharray="85 107" transform="rotate(-80 64 90)"/>
      <circle cx="135" cy="90" r="17" stroke="var(--orange)" stroke-dasharray="70 107" transform="rotate(-30 135 90)"/>
      <circle cx="205" cy="90" r="17" stroke="var(--grey)" stroke-dasharray="80 107" transform="rotate(-70 205 90)"/>
      <circle cx="64" cy="167" r="17" stroke="var(--grey)" stroke-dasharray="60 107" transform="rotate(170 64 167)"/>
      <circle cx="135" cy="167" r="17" stroke="var(--orange)" stroke-dasharray="45 107" transform="rotate(110 135 167)"/>
      <circle cx="205" cy="167" r="17" stroke="var(--grey)" stroke-dasharray="40 107" transform="rotate(190 205 167)"/>
    </g>
    <g fill="#fff" font-family="Poppins,sans-serif" font-size="7.5" font-weight="600" text-anchor="middle">
      <text x="64" y="93">1.8</text><text x="135" y="93">3.5</text><text x="205" y="93">9.5</text>
      <text x="67" y="170">30%</text><text x="135" y="170">10%</text><text x="205" y="172">34%</text>
    </g>
  </svg>
  <div class="abs" style="left:39px;top:116px;width:52px"><div class="label">HEADLINE</div><p class="small">Lorem ipsum dolor sit amet consectetur adipiscing elit, sed do</p></div>
  <div class="abs" style="left:109px;top:116px;width:52px"><div class="label">HEADLINE</div><p class="small">Lorem ipsum dolor sit amet consectetur adipiscing elit, sed do</p></div>
  <div class="abs" style="left:180px;top:116px;width:52px"><div class="label">HEADLINE</div><p class="small">Lorem ipsum dolor sit amet consectetur adipiscing elit, sed do</p></div>
  <div class="abs" style="left:37px;top:193px;width:52px"><div class="label">HEADLINE</div><p class="small">Lorem ipsum dolor sit amet consectetur adipiscing elit, sed do</p></div>
  <div class="abs" style="left:107px;top:193px;width:52px"><div class="label">HEADLINE</div><p class="small">Lorem ipsum dolor sit amet consectetur adipiscing elit, sed do</p></div>
  <div class="abs" style="left:178px;top:193px;width:52px"><div class="label">HEADLINE</div><p class="small">Lorem ipsum dolor sit amet consectetur adipiscing elit, sed do</p></div>
  <h2 class="abs head-gold" style="left:293px;top:70px;font-family:Poppins,sans-serif">Title Here</h2>
  <p class="abs body" style="left:293px;top:96px;width:120px">Lorem ipsum dolor sit amet, consectetur adipiscing elit. Etiam iaculis commodo.</p>
  <p class="abs body" style="left:293px;top:125px;width:120px">Lorem ipsum dolor sit amet, consectetur adipiscing elit. Etiam iaculis commod.</p>
  <p class="abs body" style="left:293px;top:162px;width:120px">Lorem ipsum dolor sit amet, consectetur adipiscing elit. Etiam iaculis commod.</p>
  <p class="abs body" style="left:293px;top:190px;width:120px">Lorem ipsum dolor sit amet, consectetur adipiscing elit. Etiam iaculis commod.</p>
</section>

<!-- Bars and percentage -->
<section class="slide col-left row-2">
  <div class="band"></div>
  <div class="brand-tab"><div class="brand-mark"></div><div class="brand-name"><span class="word-main">Corvane</span><span class="word-sub">Therapeutics</span></div></div>
  <p class="abs body" style="left:34px;top:46px;width:150px">Lorem ipsum dolor sit amet, consectetur adipiscing elit. Etiam iaculis commod.</p>
  <svg class="abs" style="left:0;top:0" width="451" height="253" viewBox="0 0 451 253">
    <g fill="var(--grey)">
      <rect x="42" y="150" width="4" height="20"/><rect x="49" y="136" width="4" height="34"/>
      <rect x="56" y="111" width="4" height="59"/><rect x="63" y="100" width="4" height="70"/><rect x="70" y="81" width="4" height="89"/>
    </g>
    <g fill="var(--orange)">
      <rect x="97" y="150" width="4" height="20"/><rect x="104" y="136" width="4" height="34"/>
      <rect x="111" y="111" width="4" height="59"/><rect x="118" y="100" width="4" height="70"/><rect x="125" y="81" width="4" height="89"/>
    </g>
    <circle cx="225" cy="127" r="55" fill="var(--plum-deep)" opacity=".45"/>
    <circle cx="225" cy="127" r="56" fill="none" stroke="#fff" stroke-width="1.6" stroke-dasharray="264 88" transform="rotate(-90 225 127)"/>
    <text x="225" y="133" fill="#fff" font-family="Poppins,sans-serif" font-size="21" font-weight="700" text-anchor="middle">75%</text>
    <rect x="323" y="131" width="7" height="7" fill="var(--grey)"/>
    <rect x="323" y="161" width="7" height="7" fill="var(--orange)"/>
    <line x1="34" y1="201" x2="418" y2="201" stroke="#e9cfdc" stroke-width=".7"/>
  </svg>
  <div class="abs body" style="left:34px;top:175px">Lorem ipsum</div>
  <div class="abs body" style="left:89px;top:175px">Lorem ipsum</div>
  <p class="abs body" style="left:337px;top:129px;width:90px;font-size:7px">Lorem ipsum dolor sit amet, co.</p>
  <p class="abs body" style="left:337px;top:159px;width:90px;font-size:7px">Lorem ipsum dolor sit amet, co.</p>
  <p class="abs body" style="left:34px;top:206px;width:384px;text-align:center;font-size:5.9px">Lorem ipsum dolor sit amet, consectetur adipiscing elit. Etiam iaculis commod. Lorem ipsum dolor sit amet, consectetur adipiscing elit. Etiam iaculis commod. Lorem ipsum dolor sit amet, consectetur adipiscing elit. Etiam iaculis commod.Lorem ipsum dolor sit amet, consectetur adipiscing elit. Etiam iaculis commod.</p>
</section>

<!-- Checklist and circles -->
<section class="slide col-right row-2">
  <div class="band"></div>
  <div class="brand-tab"><div class="brand-mark"></div><div class="brand-name"><span class="word-main">Corvane</span><span class="word-sub">Therapeutics</span></div></div>
  <h2 class="abs head-gold" style="left:33px;top:74px">TITLE HERE</h2>
  <svg class="abs" style="left:0;top:0" width="451" height="253" viewBox="0 0 451 253">
    <defs>
      <linearGradient id="greyBall" x1="0" y1="0" x2="1" y2="1"><stop offset="0" stop-color="#fff"/><stop offset="1" stop-color="#a9a9a9"/></linearGradient>
      <linearGradient id="orangeBall" x1="0" y1="0" x2="1" y2="1"><stop offset="0" stop-color="#f5a623"/><stop offset="1" stop-color="#ef8a12"/></linearGradient>
      <g id="tick"><rect x="-7" y="-7" width="14" height="14" rx="2" fill="none" stroke="var(--orange)" stroke-width="1.4"/><path d="M-4 0 L-1 3.5 L6 -6" fill="none" stroke="var(--orange)" stroke-width="1.8" stroke-linecap="round"/></g>
    </defs>
    <use href="#tick" x="41" y="106"/><use href="#tick" x="41" y="131"/><use href="#tick" x="41" y="156"/><use href="#tick" x="41" y="181"/>
    <circle cx="273" cy="105" r="37" fill="url(#greyBall)"/>
    <circle cx="339" cy="122" r="37" fill="#9a1f68"/>
    <circle cx="294" cy="151" r="40" fill="url(#orangeBall)"/>
    <g fill="none" stroke="#555" stroke-width=".9"><path d="M266 92h9l4 4v15h-13z"/><path d="M269 106l3-4 3 2 3-5"/></g>
    <g fill="none" stroke="#fff" stroke-width="1"><rect x="331" y="109" width="16" height="11"/><path d="M339 120v4M335 124h8M334 112h2l2 5h5l1-3"/></g>
    <g fill="none" stroke="#fff" stroke-width="1.1"><rect x="285" y="153" width="18" height="15"/><path d="M290 153v-3a4 4 0 0 1 8 0v3"/></g>
    <g fill="none" stroke="var(--orange)" stroke-width=".6"><path d="M380 80l-12 13M205 132l8-7h20M336 175l-10-6"/></g>
    <g fill="var(--orange)" font-family="Poppins,sans-serif" font-size="11" font-weight="600">
      <text x="345" y="76">32%</text><text x="226" y="154">21%</text><text x="339" y="183">45%</text>
    </g>
    <rect x="213" y="210" width="12" height="12" fill="var(--orange)"/>
    <rect x="279" y="210" width="12" height="12" fill="var(--grey)"/>
    <rect x="345" y="210" width="12" height="12" fill="var(--gold)"/>
  </svg>
  <p class="abs body" style="left:57px;top:100px;width:85px;font-size:5.5px">Lorem ipsum dolor sit amet, consectetur adipiscing elit. Etiam iaculis commodo.</p>
  <p class="abs body" style="left:57px;top:125px;width:85px;font-size:5.5px">Lorem ipsum dolor sit amet, consectetur adipiscing elit. Etiam iaculis commod.</p>
  <p class="abs body" style="left:57px;top:150px;width:85px;font-size:5.5px">Lorem ipsum dolor sit amet, consectetur adipiscing elit. Etiam iaculis commod.</p>
  <p class="abs body" style="left:57px;top:175px;width:85px;font-size:5.5px">Lorem ipsum dolor sit amet, consectetur adipiscing elit. Etiam iaculis commod.</p>
  <p class="abs small" style="left:373px;top:68px;width:55px;text-align:left;font-size:4.8px">Lorem ipsum dolor sit amet consectetur</p>
  <p class="abs small" style="left:170px;top:143px;width:55px;text-align:right;font-size:4.8px">Lorem ipsum dolor sit amet consectetur</p>
  <p class="abs small" style="left:369px;top:174px;width:55px;text-align:left;font-size:4.8px">Lorem ipsum dolor sit amet consectetur</p>
  <p class="abs small" style="left:231px;top:210px;width:40px;text-align:left;font-size:4.8px">Lorem ipsum dolor sit</p>
  <p class="abs small" style="left:297px;top:210px;width:40px;text-align:left;font-size:4.8px">Lorem ipsum dolor sit</p>
  <p class="abs small" style="left:363px;top:210px;width:40px;text-align:left;font-size:4.8px">Lorem ipsum dolor sit</p>
</section>

<!-- Market opportunities -->
<section class="slide col-left row-3">
  <div class="band"></div>
  <div class="brand-tab"><div class="brand-mark"></div><div class="brand-name"><span class="word-main">Corvane</span><span class="word-sub">Therapeutics</span></div></div>
  <svg class="abs" style="left:0;top:0" width="451" height="253" viewBox="0 0 451 253">
    <circle cx="17" cy="145" r="120" fill="#8a1b5c" stroke="#f3dbe7" stroke-width=".8"/>
    <path d="M17 145 L17 25 A120 120 0 0 1 56 32 Z" fill="var(--orange)"/>
    <path d="M17 145 L-30 35 A120 120 0 0 1 56 32 Z" fill="var(--orange)"/>
    <g stroke="#f3dbe7" stroke-width=".8">
      <line x1="17" y1="145" x2="56" y2="32"/><line x1="17" y1="145" x2="112" y2="72"/>
      <line x1="17" y1="145" x2="135" y2="160"/><line x1="17" y1="145" x2="98" y2="233"/>
    </g>
    <circle cx="17" cy="145" r="45" fill="#fff"/>
    <circle cx="17" cy="145" r="9" fill="var(--plum)"/>
    <g fill="none" stroke="#fff" stroke-width=".9">
      <path d="M23 52h8l-2 3a6 6 0 1 1-4 0z"/>
      <path d="M62 98v-5h3v5M67 98v-8h3v8M72 98v-11h3v11M60 98h17"/>
      <circle cx="89" cy="146" r="6"/><circle cx="89" cy="146" r="3"/><path d="M89 146l6-6"/>
      <ellipse cx="69" cy="196" rx="5" ry="2"/><path d="M64 196v6a5 2 0 0 0 10 0v-6"/>
      <circle cx="14" cy="219" r="2.5"/><circle cx="22" cy="219" r="2.5"/><path d="M9 227a5 4 0 0 1 10 0M17 227a5 4 0 0 1 10 0"/>
    </g>
    <g stroke="#f3dbe7" stroke-width=".7">
      <line x1="193" y1="123" x2="412" y2="123"/><line x1="193" y1="148" x2="412" y2="148"/>
      <line x1="193" y1="179" x2="412" y2="179"/><line x1="193" y1="210" x2="412" y2="210"/>
    </g>
    <g fill="none" stroke="#fff" stroke-width=".9">
      <path d="M201 94h8l-2 3a6 6 0 1 1-4 0z"/>
      <path d="M197 136v-5h3v5M202 136v-8h3v8M207 136v-11h3v11M195 136h17"/>
      <circle cx="205" cy="164" r="6"/><circle cx="205" cy="164" r="3"/><path d="M205 164l6-6"/>
      <ellipse cx="206" cy="189" rx="5" ry="2"/><path d="M201 189v8a5 2 0 0 0 10 0v-8"/>
      <circle cx="201" cy="219" r="2.5"/><circle cx="209" cy="219" r="2.5"/><path d="M196 226a5 4 0 0 1 10 0M204 226a5 4 0 0 1 10 0"/>
    </g>
  </svg>
  <h2 class="abs market-title" style="left:193px;top:59px">MARKET OPPORTUNITIES</h2>
  <div class="abs market-item" style="left:225px;top:89px;width:190px"><h4>TITLE</h4><p>It is a process to allow an organization to focus resources on the greatest opportunities to increase sales and achieve the company's target.</p></div>
  <div class="abs market-item" style="left:225px;top:127px;width:190px"><h4>TITLE</h4><p>Research your target group and narrow your market.</p></div>
  <div class="abs market-item" style="left:225px;top:152px;width:190px"><h4>TITLE</h4><p>Your brand identity is a way to tell your brand story and position yourself from your competitors visually.</p></div>
  <div class="abs market-item" style="left:225px;top:182px;width:190px"><h4>TITLE</h4><p>Marketing strategy's objective is to increase sales and gain a competitive advantage over other competitors.</p></div>
  <div class="abs market-item" style="left:225px;top:212px;width:190px"><h4>TITLE</h4><p>A new way of how we purchase goods at fingertips in modern era.</p></div>
</section>

<!-- Rings and steps -->
<section class="slide col-right row-3">
  <div class="band"></div>
  <div class="brand-tab"><div class="brand-mark"></div><div class="brand-name"><span class="word-main">Corvane</span><span class="word-sub">Therapeutics</span></div></div>
  <svg class="abs" style="left:0;top:0" width="451" height="253" viewBox="0 0 451 253">
    <defs>
      <linearGradient id="ringGrad" x1="0" y1="0" x2="1" y2="0"><stop offset="0" stop-color="#8a2a6a"/><stop offset="1" stop-color="var(--pink)"/></linearGradient>
      <linearGradient id="goldBall" x1="0" y1="0" x2="0" y2="1"><stop offset="0" stop-color="var(--gold)"/><stop offset="1" stop-color="var(--orange)"/></linearGradient>
      <g id="tick6"><rect x="-8" y="-8" width="16" height="16" rx="2" fill="none" stroke="var(--orange)" stroke-width="1.5"/><path d="M-4.5 0 L-1 4 L7 -7" fill="none" stroke="var(--orange)" stroke-width="2" stroke-linecap="round"/></g>
    </defs>
    <g fill="none" stroke="url(#ringGrad)" stroke-width="2.2">
      <circle cx="90" cy="143" r="68"/><circle cx="90" cy="143" r="56"/><circle cx="90" cy="143" r="43"/><circle cx="90" cy="143" r="30"/>
    </g>
    <circle cx="193" cy="86" r="14.5" fill="#9a1f68"/>
    <circle cx="193" cy="123" r="14.5" fill="#5e0f40"/>
    <circle cx="193" cy="161" r="14.5" fill="url(#goldBall)"/>
    <circle cx="193" cy="197" r="14.5" fill="url(#goldBall)"/>
    <use href="#tick6" x="313" y="111"/><use href="#tick6" x="313" y="141"/><use href="#tick6" x="313" y="170"/><use href="#tick6" x="313" y="200"/>
  </svg>
  <div class="abs" style="left:220px;top:74px"><div class="num">01</div><p class="small" style="text-align:left;width:55px;font-size:4.6px">Lorem ipsum dolor sit amet consectetur adipiscing elit, sed do</p></div>
  <div class="abs" style="left:220px;top:110px"><div class="num">02</div><p class="small" style="text-align:left;width:55px;font-size:4.6px">Lorem ipsum dolor sit amet consectetur adipiscing elit, sed do</p></div>
  <div class="abs" style="left:220px;top:147px"><div class="num">03</div><p class="small" style="text-align:left;width:55px;font-size:4.6px">Lorem ipsum dolor sit amet consectetur adipiscing elit, sed do</p></div>
  <div class="abs" style="left:220px;top:184px"><div class="num">04</div><p class="small" style="text-align:left;width:55px;font-size:4.6px">Lorem ipsum dolor sit amet consectetur adipiscing elit, sed do</p></div>
  <h2 class="abs head-gold" style="left:303px;top:76px">TITLE HERE</h2>
  <p class="abs body" style="left:332px;top:104px;width:100px;font-size:6px">Lorem ipsum dolor sit amet, consectetur adipiscing elit. Etiam iaculis commodo.</p>
  <p class="abs body" style="left:332px;top:134px;width:100px;font-size:6px">Lorem ipsum dolor sit amet, consectetur adipiscing elit. Etiam iaculis commod.</p>
  <p class="abs body" style="left:332px;top:163px;width:100px;font-size:6px">Lorem ipsum dolor sit amet, consectetur adipiscing elit. Etiam iaculis commod.</p>
  <p class="abs body" style="left:332px;top:193px;width:100px;font-size:6px">Lorem ipsum dolor sit amet, consectetur adipiscing elit. Etiam iaculis commod.</p>
</section>

</body>
</html>
```